Corporate Business Card

Very professional, Modern, Not to busy, include phone address email, website
(253) 617-4930, 18761 52nd Avenue S, Kent, WA 98047, martin@plumlinegroup.com, varkoworks.com

Target Market(s)

Manufacturing

Industry/Entity Type

Aero, machining, manufacturing, Off road racing

Contact Information for Business Card

Phone, address email, website

```html
<!DOCTYPE html>
<html lang="en">
<head>
<meta charset="utf-8">
<title>Varko Works – Business Card</title>
<link rel="stylesheet" href="https://fonts.googleapis.com/css2?family=Montserrat:wght@500;700&display=swap">
<style>
  :root {
    --navy: #163a72;
    --red: #d7252d;
    --silver: #cfd1d4;
    --white: #ffffff;
    --ink: #111111;
    --backdrop: #1e1e1e;
  }
  * { margin: 0; padding: 0; box-sizing: border-box; }
  html, body { width: 1200px; height: 927px; overflow: hidden; }
  body {
    background: var(--backdrop);
    font-family: "Montserrat", Arial, sans-serif;
    position: relative;
  }
  .card {
    position: absolute;
    left: 250px;
    width: 700px;
    height: 400px;
    border-radius: 26px;
    overflow: hidden;
  }
  .card--front { top: 40px; background: var(--navy); }
  .card--back { top: 487px; background: var(--white); }

  .brand-name {
    position: absolute;
    font-weight: 700;
    letter-spacing: 1px;
    white-space: nowrap;
  }
  .card--front .brand-name {
    left: 0; right: 0; top: 160px;
    text-align: center;
    font-size: 66px;
    color: var(--silver);
  }
  .card--back .brand-name {
    right: 48px; top: 62px;
    font-size: 44px;
    color: var(--navy);
  }

  .address {
    position: absolute;
    left: 58px; top: 150px;
    font-size: 18px;
    font-weight: 500;
    line-height: 1.4;
    color: var(--ink);
  }
  .contact-list {
    position: absolute;
    left: 62px; top: 222px;
    list-style: none;
    font-size: 18px;
    font-weight: 500;
    color: var(--ink);
  }
  .contact-list li {
    display: flex;
    align-items: center;
    gap: 10px;
    height: 28px;
  }
  .contact-icon { width: 18px; height: 18px; flex: none; }
  .footer-bands { position: absolute; left: 0; top: 0; width: 700px; height: 400px; }
</style>
</head>
<body>
  <section class="card card--front">
    <div class="brand-name">Varko Works</div>
  </section>

  <section class="card card--back">
    <div class="brand-name">Varko Works</div>

    <address class="address" style="font-style: normal;">
      18761 52nd Avenue S,<br>Kent, WA 98047
    </address>

    <ul class="contact-list">
      <li>
        <svg class="contact-icon" viewBox="0 0 20 20" aria-hidden="true">
          <path fill="var(--red)" d="M5 2c1-1 2 0 3 1.5l1 2c.5 1 0 1.7-.7 2.3-.6.5-.4 1.2.3 2.2s1.6 1.8 2.4 2.2c.8.4 1.4.1 1.8-.6.6-.8 1.4-1 2.3-.4l1.9 1.2c1.3.9 1.3 2 .3 3-1.7 1.7-4.5 1.4-8-1.8S1.3 7 2.9 4.3C3.5 3.3 4.2 2.6 5 2z"/>
        </svg>
        (253) 617-4930
      </li>
      <li>
        <svg class="contact-icon" viewBox="0 0 20 20" aria-hidden="true">
          <rect x="1" y="4" width="18" height="12" rx="1.5" fill="var(--red)"/>
          <path d="M2 5.5l8 6 8-6" fill="none" stroke="var(--white)" stroke-width="1.6"/>
        </svg>
        martin@plumlinegroup.com
      </li>
      <li>
        <svg class="contact-icon" viewBox="0 0 20 20" aria-hidden="true">
          <circle cx="10" cy="10" r="9" fill="var(--red)"/>
          <circle cx="10" cy="10" r="6" fill="none" stroke="var(--white)" stroke-width="1.3"/>
          <path d="M4 10h12M10 4c-3 3-3 9 0 12M10 4c3 3 3 9 0 12" fill="none" stroke="var(--white)" stroke-width="1.3"/>
        </svg>
        www.varkoworks.com
      </li>
    </ul>

    <svg class="footer-bands" viewBox="0 0 700 400" aria-hidden="true">
      <polygon fill="var(--red)" points="0,336 245,336 239,346 0,346"/>
      <polygon fill="var(--navy)" points="253,336 470,336 464,346 247,346"/>
      <polygon fill="var(--red)" points="478,336 590,336 584,346 472,346"/>
      <polygon fill="var(--navy)" points="0,354 592,354 612,318 622,300 700,300 700,400 0,400"/>
    </svg>
  </section>
</body>
</html>
```